Take Sunward Path Now Road Tour

I need a Chatterbox cover photo design for my holisitic health and wellness campaign "Take Sunward Path Now."

-Purpose: Quest to find a healthier me through career, relationships and food
-Documentary (Similar to the documentary "Tired Stuck and Barely Well")- interviewing professionals along the way in the field I work in, the entertainment industry, on health and wellness as it relates to career, relationships and food. We will also capture footage from my mom, phone calls from friends, pre planning, meditation, me working while on the road, farmers market trips, healthy restaurants, music venues and plays.
-Cities and States we will visit: Lincoln, Nebraska; Denver, Colorado; Las Vegas, Nevada; Studio City, California
Timeline and Distance: Over 2000 miles, over 31 hours, over the course of 5 days (Sept 12th-16th.
-Interesting fact #1: I sold everything, even my car and I'm relocating to California for this quest for a healthier happier me.
-Interesting fact #2: My mom from Maryland is flying in this friday to support me and drive as well.
-Interesting fact #3: I am currently in nutrition school to be a certified health coach
-We are encouraging our Chatterbox fans to follow us on our chatterbox pages as well. -Donations: Followers can also donate to the campaign on our fundwell page. All proceeds will go to me starting a business in helping professionals in my industry live longer healthier lives through career, relationships and food.

WHAT I"M LOOKING FOR
I would like to see designs that are fun. The design when seen by viewers on Chatterbox should tell a story of me on a quest for a healthier me, selling everything I own, hopping in a car and driving through the various cities to find my truest self. The final design should communicate a road being taken to the healthier happier me through career, relationships and food.
Updates

The name of the campaign is "Take Sunward Path Now" Also the campaign to raise funds for those interested will be posted on my website, once the creative is completed at www.KTRholdings.example. Thank you all! I am looking forward to seeing your work! Marisol T.

Update to cities and states 1) Lincoln, Nebraska 2) Denver, Colorado 3) Albuquerque, New Mexico 4) Las Vegas, Nevada 5) Studio City, California

Target Market(s)

Entertainment Professionals who eventually will want me to coach them in their careers, relationships and with food.

Industry/Entity Type

Entertainment

```html
<!DOCTYPE html>
<html lang="en">
<head>
<meta charset="utf-8">
<title>Take Sunward Path Now — Road Tour Cover</title>
<link rel="stylesheet" href="https://fonts.googleapis.com/css2?family=Passion+One:wght@400;700&family=Oswald:wght@500&family=Luckiest+Guy&family=Archivo+Narrow:wght@400;500&display=swap">
<style>
  :root {
    --bg-light: #eceeb4;
    --bg-mid: #dcdf97;
    --bg-deep: #c9cf72;
    --ink: #1b1b18;
    --road-orange: #f2621f;
    --hill-black: #161616;
    --white: #ffffff;
    --stop-tone-stone: #b9a98c;
    --stop-tone-sky: #9fb6a8;
    --stop-tone-adobe: #b0744e;
    --stop-tone-blue: #7f9fb3;
    --stop-tone-grey: #8c8f86;
    --stop-tone-steel: #9aa1a3;
  }
  * { box-sizing: border-box; margin: 0; padding: 0; }
  html, body { width: 1200px; height: 444px; overflow: hidden; background: #ffffff; }
  .cover {
    position: relative;
    width: 1200px;
    height: 444px;
    overflow: hidden;
    background: radial-gradient(ellipse at 40% 40%, var(--bg-light) 0%, var(--bg-mid) 55%, var(--bg-deep) 100%);
    font-family: "Archivo Narrow", "Arial Narrow", sans-serif;
    color: var(--ink);
  }
  .campaign-title {
    position: absolute;
    left: 18px;
    top: 58px;
    width: 230px;
    text-align: center;
    font-family: "Passion One", "Impact", sans-serif;
    font-weight: 700;
    line-height: 0.88;
    text-transform: uppercase;
    color: var(--ink);
  }
  .campaign-title .line-small { display: block; font-size: 38px; letter-spacing: 0.5px; }
  .campaign-title .line-big { display: block; font-size: 70px; }
  .tour-headline {
    position: absolute;
    right: 30px;
    top: 30px;
    font-family: "Oswald", "Arial Narrow", sans-serif;
    font-weight: 500;
    font-size: 31px;
    letter-spacing: 0.4px;
    text-transform: uppercase;
  }
  .tour-dates {
    position: absolute;
    right: 30px;
    top: 76px;
    font-family: "Luckiest Guy", "Impact", sans-serif;
    font-size: 27px;
    letter-spacing: 1px;
    transform: skewX(-8deg);
  }
  .stop-label {
    position: absolute;
    text-align: center;
    font-size: 16px;
    line-height: 1.2;
    transform: translateX(-50%);
    white-space: nowrap;
  }
  .stop-scene { position: absolute; border-radius: 3px; }
  .road-art { position: absolute; left: 0; top: 0; }
  .road-tagline {
    font-family: "Oswald", "Arial Narrow", sans-serif;
    font-weight: 500;
    font-size: 18px;
    fill: var(--white);
    text-transform: uppercase;
  }
  .road-story {
    position: absolute;
    left: 846px;
    top: 376px;
    transform: translateX(-50%);
    text-align: center;
    color: var(--white);
    font-size: 18px;
    line-height: 27px;
    white-space: nowrap;
  }
</style>
</head>
<body>
<main class="cover">

  <h1 class="campaign-title">
    <span class="line-small">Take Sunward</span>
    <span class="line-big">Path</span>
    <span class="line-big">Now</span>
  </h1>

  <p class="tour-headline">Mom and Daughter, 4 Days, Over 2000 Miles</p>
  <p class="tour-dates">(Sept 12th–16th)</p>

  <p class="stop-label" style="left:318px; top:208px;">Studio City<br>California<br>(16 Sept)</p>
  <p class="stop-label" style="left:452px; top:196px;">Las Vegas<br>Nevada<br>(15 Sept)</p>
  <p class="stop-label" style="left:610px; top:182px;">Albuquerque<br>New Mexico<br>(14 Sept)</p>
  <p class="stop-label" style="left:764px; top:214px;">Denver<br>Colorado<br>(13 Sept)</p>
  <p class="stop-label" style="left:888px; top:166px;">Lincoln<br>Nebraska<br>(12 Sept)</p>
  <p class="stop-label" style="left:1062px; top:184px;">Starting from<br>Chicago, IL</p>

  <div class="stop-scene" role="img" aria-label="Studio City welcome sign" style="left:276px; top:290px; width:98px; height:60px; background:linear-gradient(var(--stop-tone-stone), var(--stop-tone-grey));"></div>
  <div class="stop-scene" role="img" aria-label="Las Vegas welcome sign with palm trees" style="left:402px; top:276px; width:114px; height:74px; background:linear-gradient(var(--stop-tone-sky), #c9b86a);"></div>
  <div class="stop-scene" role="img" aria-label="Albuquerque adobe mission church" style="left:543px; top:262px; width:134px; height:88px; background:linear-gradient(#c78f68, var(--stop-tone-adobe));"></div>
  <div class="stop-scene" role="img" aria-label="Denver painted cow sculpture" style="left:712px; top:296px; width:106px; height:54px; background:linear-gradient(var(--stop-tone-blue), #d9c37a);"></div>
  <div class="stop-scene" role="img" aria-label="Lincoln state capitol skyline" style="left:826px; top:226px; width:134px; height:124px; background:linear-gradient(#b4b6ad, var(--stop-tone-grey));"></div>
  <div class="stop-scene" role="img" aria-label="Chicago skyline, mirrored sculpture and a small red car" style="left:988px; top:246px; width:212px; height:134px; background:linear-gradient(100deg, var(--stop-tone-steel), #b9bdb7 60%, #c94a3c);"></div>

  <svg class="road-art" width="1200" height="444" viewBox="0 0 1200 444" aria-hidden="true">
    <path d="M215 444 Q640 276 1200 343 L1200 444 Z" fill="var(--hill-black)"/>
    <path d="M237 444 Q640 290 1200 352 L1200 444 Z" fill="var(--road-orange)"/>
    <path id="road-line" d="M322 432 Q640 350 1200 362" fill="none"/>
    <text class="road-tagline">
      <textPath href="#road-line" startOffset="4" textLength="870" lengthAdjust="spacing">A road to the healthier happier me through career, relationships and food</textPath>
    </text>
  </svg>

  <p class="road-story">Selling everything, hopping in a car<br>driving through the various cities to find truest self</p>

</main>
</body>
</html>
```